Event flyer for Sunday night Youth Group

Need a 4 x 6 or 5 x 7 flyer for a new youth group starting on April 14. The youth group is for students in middle school and high school so it needs to look fun and cool, but not childish. I prefer it not to include pictures of people unless it's so obscure you can't really see their faces. I've uploaded some pictures of flyers I like. I've also attached a couple versions of our logo to use on the flyer.
Information the flyer needs to include:
Youth Group
Sundays, 6-8pm (beginning April 14)
Location: Marlowe's - 4219 Quarry Fern Ave N, Keizer, 97318
There will be dinner, games, friends, and a message.
Target Market(s)
Youth ages 13-18
Industry/Entity Type
Church
Font styles to use
Colors
Designer to choose colors to be used in the design.
Look and feel

```html
<!DOCTYPE html>
<html lang="en">
<head>
<meta charset="utf-8">
<title>Youth Group Flyer</title>
<link rel="stylesheet" href="https://fonts.googleapis.com/css2?family=Oswald:wght@500;600&family=Roboto+Condensed:wght@400;700&display=swap">
<style>
  :root {
    --stage: #383836;
    --yellow: #ffe01b;
    --purple-deep: #24185a;
    --purple-mid: #4a2a6e;
    --wine: #7a3a4e;
    --white: #ffffff;
    --ink: #1c1c1c;
    --orange: #e8602a;
    --slate: #243f4f;
  }
  html, body {
    margin: 0;
    width: 1200px;
    height: 2473px;
    overflow: hidden;
    background: var(--stage);
  }
  .flyer {
    position: absolute;
    left: 0;
    top: 396px;
    width: 1200px;
    height: 1681px;
    display: block;
  }
  .headline-light { font-family: "Oswald", sans-serif; font-weight: 500; fill: var(--white); }
  .headline-bold { font-family: "Oswald", sans-serif; font-weight: 600; fill: var(--yellow); }
  .schedule { font-family: "Roboto Condensed", sans-serif; font-weight: 700; fill: var(--white); }
  .start-date { font-family: "Roboto Condensed", sans-serif; font-weight: 400; fill: var(--yellow); }
  .start-date .emph { font-weight: 700; }
  .address { font-family: "Roboto Condensed", sans-serif; font-weight: 400; fill: var(--ink); }
  .activities { font-family: "Roboto Condensed", sans-serif; font-weight: 400; fill: var(--orange); }
  .org-name { font-family: "Roboto Condensed", sans-serif; font-weight: 700; fill: var(--slate); letter-spacing: 1px; }
</style>
</head>
<body>
<svg class="flyer" viewBox="0 0 666 933" xmlns="http://www.w3.org/2000/svg">
  <defs>
    <linearGradient id="venueTone" x1="0" y1="0" x2="0.3" y2="1">
      <stop offset="0" stop-color="var(--purple-deep)"/>
      <stop offset="0.55" stop-color="var(--purple-mid)"/>
      <stop offset="1" stop-color="var(--wine)"/>
    </linearGradient>
    <linearGradient id="footerFade" x1="0" y1="603" x2="0" y2="860" gradientUnits="userSpaceOnUse">
      <stop offset="0" stop-color="var(--yellow)"/>
      <stop offset="0.8" stop-color="var(--white)"/>
    </linearGradient>
  </defs>

  <rect class="venue-photo" role="img" aria-label="Dim church interior with wooden pews and arched stained-glass windows, tinted purple" x="0" y="0" width="666" height="933" fill="url(#venueTone)"/>

  <path class="top-wave" d="M0,0 L51,0 C300,40 570,170 580,228 C588,262 380,300 0,373 Z" fill="var(--yellow)"/>
  <path class="top-wave-line" d="M0,18 C280,60 560,170 565,225 C568,255 350,290 0,355" fill="none" stroke="var(--white)" stroke-width="0.8"/>

  <path class="side-lens" d="M666,433 C610,455 556,485 556,500 C556,520 610,555 666,583 Z" fill="var(--yellow)"/>
  <path class="side-lens-line" d="M666,443 C620,465 566,490 566,500 C566,515 620,548 666,573" fill="none" stroke="var(--white)" stroke-width="0.8"/>

  <path class="footer-wave" d="M0,603 C180,700 420,780 666,848 L666,933 L0,933 Z" fill="url(#footerFade)"/>
  <path class="footer-wave-line" d="M0,675 C200,720 420,780 666,865" fill="none" stroke="var(--white)" stroke-width="0.8"/>

  <rect class="org-mark" x="176" y="100" width="34" height="34" fill="var(--slate)"/>
  <text class="org-name" x="193" y="236" text-anchor="middle" font-size="30">WAYPOINT</text>
  <text class="org-name" x="193" y="265" text-anchor="middle" font-size="17" letter-spacing="6">FELLOWSHIP</text>

  <text class="headline-light" x="548" y="435" text-anchor="end" font-size="124">YOUTH</text>
  <text class="headline-bold" x="548" y="598" text-anchor="end" font-size="205" textLength="500" lengthAdjust="spacingAndGlyphs">GROUP</text>
  <text class="schedule" x="548" y="655" text-anchor="end" font-size="48">SUNDAYS, 6-8PM</text>
  <text class="start-date" x="548" y="691" text-anchor="end" font-size="27">beginning <tspan class="emph">April 14</tspan></text>

  <text class="address" x="41" y="791" font-size="23">Marlowe's - 4219</text>
  <text class="address" x="41" y="821" font-size="23">Quarry Fern Ave N, Keizer, 97318</text>

  <line class="rule" x1="135" y1="854" x2="533" y2="854" stroke="var(--ink)" stroke-width="0.8" stroke-dasharray="1.5 2"/>
  <text class="activities" x="334" y="883" text-anchor="middle" font-size="24">DINNER | GAMES | FRIENDS | MESSAGE</text>
  <line class="rule" x1="135" y1="894" x2="533" y2="894" stroke="var(--ink)" stroke-width="0.8" stroke-dasharray="1.5 2"/>
</svg>
</body>
</html>
```